New business blog needs wordpress theme

I need a unique wordpress theme for my new business oriented blog at hollowpeakdesk.com. The blog focuses on my experience as an entrepreneur and offers insights into business problems while chronicling my experience building a new company.

I would like to see a theme that looks more like a creative professional's website, not a business website. Large photos, bright colors, unique layout. I do not want stock photos of people in suits doing business type things. Also, no pictures of me - I am blogging anonymously.

The design should communicate technology and beauty - for example, I really like the feel of the landing page at www.tundrelo.com - it is beautiful to look at but also reflects the cutting edge nature of what they are doing.

Industry/Entity Type

Business

```html
<!DOCTYPE html>
<html lang="en">
<head>
<meta charset="utf-8">
<title>Hollow Peak — Business Blog</title>
<link href="https://fonts.googleapis.com/css2?family=Open+Sans:wght@400;600;700&display=swap" rel="stylesheet">
<style>
:root{
  --blue:#1e5c9c;
  --link:#1f5fa3;
  --page:#ececec;
  --green-dark:#4f7e16;
  --green:#74a427;
  --note:#fdfbc9;
  --note-line:#ebe6ad;
  --note-fold:#d9bd62;
  --text:#555;
  --footer:#2b2b2b;
  --footer-bottom:#1d1d1d;
  --footer-text:#8a8a8a;
}
*{margin:0;padding:0;box-sizing:border-box}
html,body{width:723px;height:1200px;overflow:hidden}
body{position:relative;background:var(--page);font-family:'Open Sans',sans-serif;color:var(--text)}
.abs{position:absolute}
.site-header{position:absolute;left:0;top:0;width:723px;height:50px;background:var(--blue)}
.logo{position:absolute;left:61px;top:13px;color:#fff;font-size:18px;font-weight:400;letter-spacing:.3px}
.nav{position:absolute;top:18px;left:230px}
.nav a{color:#fff;font-size:8px;text-decoration:none;text-transform:uppercase;position:absolute;top:3px;white-space:nowrap}
.nav .active{background:#fff;color:var(--blue);border-radius:2px;top:0;padding:3px 0;width:40px;text-align:center}
.search{position:absolute;left:545px;top:14px;width:116px;height:21px;background:#fff;border:1px solid #cfd8e2}
.search span{position:absolute;left:8px;top:5px;font-size:6.5px;color:#aaa;font-style:italic}
.search svg{position:absolute;right:0;top:0;border-left:1px solid #ddd}
.hero{position:absolute;left:61px;top:64px;width:599px;height:261px;background:radial-gradient(circle at 38% 45%,#95c23e 0%,var(--green) 35%,var(--green-dark) 100%);box-shadow:0 4px 10px rgba(0,0,0,.25)}
.hero-art{position:absolute;left:16px;top:20px;width:300px;height:240px;background:radial-gradient(ellipse at 55% 50%,rgba(220,235,200,.45),rgba(255,255,255,0) 65%)}
.hero-text{position:absolute;left:328px;top:103px;color:#fff}
.hero-text h2{font-size:14px;font-weight:400;line-height:17px}
.hero-text p{font-size:10px;line-height:12.5px}
.btn{position:absolute;left:328px;top:150px;width:69px;height:21px;background:var(--blue);color:#fff;font-size:7.5px;text-align:center;line-height:21px}
.dots{position:absolute;left:538px;top:238px}
.dots i{position:absolute;width:7px;height:7px;border-radius:50%;background:#2a3c1a}
.dots i.on{background:#2a6db0;border:1.5px solid #1c3a55}
.content{position:absolute;left:61px;top:325px;width:599px;height:753px;background:#fff}
.post-title{position:absolute;left:84px;color:var(--link);font-size:13.5px;font-weight:400;line-height:16.5px;white-space:nowrap}
.meta{position:absolute;left:84px;font-size:7.5px;color:#555}
.meta b{color:#333;font-weight:600}
.meta a{color:var(--link)}
.txt{position:absolute;font-size:7.6px;line-height:9.5px;text-align:justify;color:#666}
.txt p{margin-bottom:5px}
.subhead{position:absolute;left:84px;top:444px;font-size:10.5px;font-weight:600;color:#555}
.more{position:absolute;left:84px;width:346px;height:10px}
.more::before{content:"";position:absolute;left:0;right:57px;top:6px;border-top:1px dotted #999}
.more span{position:absolute;right:2px;top:0;font-size:8px;color:var(--link)}
.thumb{position:absolute}
.scroll{position:absolute;left:232px;top:1047px;font-size:7px;color:#333;width:50px;text-align:center}
.sidebar{position:absolute;left:453px;top:348px;width:183px;height:730px;background:var(--note)}
.side-h{position:absolute;left:472px;font-size:13px;font-weight:400;color:#333}
.side-item{position:absolute;left:485px;font-size:7.8px;line-height:9.2px;color:var(--link);width:140px}
.rule{position:absolute;left:468px;width:153px;height:1px;background:var(--note-line)}
.footer{position:absolute;left:0;top:1078px;width:723px;height:94px;background:var(--footer)}
.foot-bottom{position:absolute;left:0;top:1172px;width:723px;height:28px;background:var(--footer-bottom)}
.foot-h{position:absolute;color:#2a72b8;font-size:9.5px;font-weight:600}
.foot-list{position:absolute;color:var(--footer-text);font-size:6.6px;line-height:8.1px;text-transform:uppercase}
.vline{position:absolute;top:1097px;width:1px;height:66px;background:#444}
.social{position:absolute;top:1093px;width:13px;height:13px;border-radius:50%;background:#8f8f8f}
.copy{position:absolute;left:442px;top:1182px;font-size:6.5px;color:#666}
</style>
</head>
<body>

<header class="site-header">
  <div class="logo">HOLLOW PEAK</div>
  <nav class="nav">
    <a class="active" style="left:0">Home</a>
    <a style="left:44px">Small Business</a>
    <a style="left:122px">Technology</a>
    <a style="left:188px">About Daniel</a>
    <a style="left:265px">Contact</a>
  </nav>
  <div class="search"><span>SEARCH</span>
    <svg width="20" height="19" viewBox="0 0 20 19"><circle cx="9" cy="8" r="4.2" fill="none" stroke="#555" stroke-width="1.8"/><line x1="12" y1="11" x2="15.5" y2="14.5" stroke="#555" stroke-width="2.2" stroke-linecap="round"/></svg>
  </div>
</header>

<section class="hero">
  <div class="hero-art" role="img" aria-label="Blurred man drawing a globe surrounded by world landmarks"></div>
  <div class="hero-text">
    <h2>Daniel talks business. Best practices</h2>
    <p>articles and tips and about small business<br>in the United States</p>
  </div>
  <div class="btn">KNOW MORE</div>
  <div class="dots"><i class="on" style="left:0"></i><i style="left:16px"></i><i style="left:30px"></i><i style="left:43px"></i></div>
</section>

<main class="content"></main>

<!-- Post 1 -->
<h1 class="post-title" style="top:349px">Comparing Direct Mail to Dealbloom – By the Numbers</h1>
<div class="meta" style="top:372px">Posted on <b>March 6, 2014</b> by Daniel — <a>Leave a comment</a></div>
<div class="txt" style="left:84px;top:403px;width:346px">
  <p>Unhappy with the results of a direct mail (snail mail) campaign, I decided to compare the results to a Dealbloom campaign. I compared both the cost of the respective campaigns, the revenue generated, the customers acquired and customer retention.</p>
</div>
<div class="subhead">Background</div>
<div class="txt" style="left:84px;top:466px;width:346px">
  <p>One of my businesses owns and operates franchised hair salons. We have 15 salons across 2 different brands. The company builds new salons and buys and rehabilitates old salons. One brand is a value focused family salon, the other is a high-end male oriented barbershop.</p>
  <p>When I open a new barbershop, I set a goal of 350 customers in the first month. Over 12+ months, I want to build that to 1,000+ customers per month.</p>
</div>
<div class="more" style="top:534px"><span>Read full post</span></div>

<!-- Post 2 -->
<h1 class="post-title" style="top:562px">Finally Dumping Gabble Chat on Orbit OS<br>– Any Recommendations for an SMS App?</h1>
<div class="meta" style="top:601px">Posted on <b>March 6, 2014</b> by Daniel — <a>Leave a comment</a></div>
<div class="thumb" style="left:84px;top:630px;width:95px;height:140px;background:linear-gradient(180deg,#f8b524 0%,#f6ac1c 70%,#8cc13f 85%,#f6ac1c 100%)" role="img" aria-label="Orange book cover with a cartoon crocodile"></div>
<div class="txt" style="left:190px;top:629px;width:240px">
  <p>I am embarrassed how long I tried to make Gabble Chat work on Orbit OS. Gabble Chat is Gabble's default SMS client for Orbit OS 4. It combines SMS with Gabble's chat/video product called Gabble Chat. Online, Gabble Chat is excellent. It allows you to chat or video with your gabble contacts, collaboratively work on web documents, have group video chats, etc. On the phone it is painfully slow. Trying to view or send out a text message can take forever.</p>
  <p>All my business run on Gabble – email, documents, spreadsheets, chat, video – I am drinking the fruit punch and I love it. It is cheap and works. In the past I have used a full Northwind stack (Relay Mail, file servers, NW Office) and found it expensive to install and maintain and required a lot of employee training. For the most part, I love how Gabble Suite for Business just works.</p>
</div>
<div class="more" style="top:787px"><span>Read full post</span></div>

<!-- Post 3 -->
<h1 class="post-title" style="top:816px">The Who &amp; The Why</h1>
<div class="meta" style="top:836px">Posted on <b>March 6, 2014</b> by Daniel — <a>Leave a comment</a></div>
<div class="thumb" style="left:84px;top:862px;width:116px;height:83px;background:linear-gradient(180deg,#4f86c6 0%,#8db4dc 45%,#8a7a52 60%,#5a5344 100%)" role="img" aria-label="Desert highway with a roadside sign under a blue sky"></div>
<div class="txt" style="left:211px;top:862px;width:219px">
  <p>I started this blog to share much of the knowledge that I have built up during the last 20 years as an entrepreneur. With all of my businesses, I continually run experiments on what works best. I usually summarize my results in little notes to myself – my hope is to share much of that with you. I also hope to learn a lot from the community of entrepreneurs out there.I blog anonymously so that I can keep my business interests separate from this hobby. If you contact me, however, I will reply as myself.</p>
</div>
<div class="txt" style="left:84px;top:955px;width:346px">
  <p style="margin-bottom:0">I am a San Francisco based entrepreneur and attorney who has founded and managed several successful businesses.</p>
  <p>I am the owner/operator of franchised hair salons, a company I founded in 2013. The company now has 15 salons open and in development and employs over 100 people. In addition, I am building a new technology startup in the small business communication and administration field.</p>
</div>
<div class="more" style="top:1020px"><span>Read full post</span></div>
<div class="scroll">SCROLL DOWN<br>
  <svg width="10" height="6" viewBox="0 0 10 6"><polyline points="1,1 5,5 9,1" fill="none" stroke="#333" stroke-width="1"/></svg>
</div>

<!-- Sidebar -->
<aside class="sidebar"></aside>
<svg class="abs" style="left:453px;top:345px" width="184" height="8" viewBox="0 0 184 8"><path d="M0 8 Q4 2 8 8 Q12 2 16 8 Q20 2 24 8 Q28 2 32 8 Q36 2 40 8 Q44 2 48 8 Q52 2 56 8 Q60 2 64 8 Q68 2 72 8 Q76 2 80 8 Q84 2 88 8 Q92 2 96 8 Q100 2 104 8 Q108 2 112 8 Q116 2 120 8 Q124 2 128 8 Q132 2 136 8 Q140 2 144 8 Q148 2 152 8 L184 8 Z" fill="#fdfbc9"/></svg>
<svg class="abs" style="left:609px;top:347px" width="28" height="53" viewBox="0 0 28 53"><polygon points="0,0 28,27 28,53 0,27" fill="#efe8b5"/><polygon points="0,0 28,27 0,27" fill="var(--note-fold)"/></svg>

<h3 class="side-h" style="top:364px">Recent Posts</h3>
<svg class="abs" style="left:468px;top:402px" width="12" height="12" viewBox="0 0 12 12"><path d="M2 2 L10 10 M1 1 L3 1 L3 3 Z" stroke="#222" stroke-width="2" fill="#222"/></svg>
<div class="side-item" style="top:399px">Comparing Direct Mail to Dealbloom By the Numbers</div>
<div class="rule" style="top:421px"></div>
<svg class="abs" style="left:468px;top:431px" width="12" height="12" viewBox="0 0 12 12"><path d="M2 2 L10 10 M1 1 L3 1 L3 3 Z" stroke="#222" stroke-width="2" fill="#222"/></svg>
<div class="side-item" style="top:428px">Finally Dumping Gabble Chat on Orbit OS – Any Recommendations for an SMS App?</div>
<div class="rule" style="top:459px"></div>
<svg class="abs" style="left:468px;top:465px" width="12" height="12" viewBox="0 0 12 12"><path d="M2 2 L10 10 M1 1 L3 1 L3 3 Z" stroke="#222" stroke-width="2" fill="#222"/></svg>
<div class="side-item" style="top:466px">The Who &amp; The Why</div>
<div class="rule" style="top:487px"></div>
<div class="rule" style="top:508px"></div>

<h3 class="side-h" style="top:512px">Top Posts by Clicks</h3>
<svg class="abs" style="left:471px;top:544px" width="8" height="8"><circle cx="4" cy="4" r="2.6" fill="none" stroke="#2a6db0" stroke-width="1.4"/></svg>
<div class="side-item" style="top:543px">hollowpeakdesk.com</div>
<div class="rule" style="top:557px"></div>
<div class="rule" style="top:568px"></div>

<h3 class="side-h" style="top:578px">Links</h3>
<div class="rule" style="top:606px"></div>
<svg class="abs" style="left:471px;top:608px" width="8" height="8"><circle cx="4" cy="4" r="2.6" fill="none" stroke="#2a6db0" stroke-width="1.4"/></svg>
<div class="side-item" style="top:607px">RSS Feed</div>
<div class="rule" style="top:628px"></div>
<div class="rule" style="top:648px"></div>
<div class="rule" style="top:668px"></div>
<div class="rule" style="top:688px"></div>
<div class="rule" style="top:708px"></div>
<div class="rule" style="top:728px"></div>
<div class="rule" style="top:748px"></div>
<div class="rule" style="top:768px"></div>
<div class="rule" style="top:788px"></div>
<div class="rule" style="top:808px"></div>
<div class="rule" style="top:828px"></div>
<div class="rule" style="top:848px"></div>
<div class="rule" style="top:868px"></div>
<div class="rule" style="top:888px"></div>
<div class="rule" style="top:908px"></div>
<div class="rule" style="top:928px"></div>
<div class="rule" style="top:948px"></div>
<div class="rule" style="top:968px"></div>
<div class="rule" style="top:988px"></div>
<div class="rule" style="top:1008px"></div>
<div class="rule" style="top:1028px"></div>
<div class="rule" style="top:1048px"></div>

<!-- Footer -->
<footer class="footer"></footer>
<div class="foot-bottom"></div>
<div class="foot-h" style="left:78px;top:1094px">CONTACT</div>
<div class="foot-list" style="left:78px;top:1111px">Hollow Peak<br>Cedar Falls, BC V0X 1A2<br>British Columbia, Canada<br><br>Phone: 555.014.2290<br>Email: info@hollowpeakdesk.com</div>
<div class="vline" style="left:219px"></div>
<div class="foot-h" style="left:245px;top:1097px">MENU LINKS</div>
<div class="foot-list" style="left:245px;top:1114px">Small Business<br>Technology<br>About Me<br>Conact<br>Privacy Policy</div>
<div class="vline" style="left:338px"></div>
<div class="social" style="left:596px"></div>
<div class="social" style="left:612px"></div>
<div class="social" style="left:629px"></div>
<div class="copy">© COPYRIGHT 2014 . ALL RIGHTS RESERVED TO HOLLOW PEAK</div>

</body>
</html>
```